6 page (for now) squarespace website design for a Mobile Fitness small business

My sons California based small business "BrenVale Coaching" with new subsidiary called "BrenVale 4 Kids". I don't understand coding the website, is that the function squarespace provides?
In the end I want a working website, squarespace, I have a google workspace domain, email and subscription to squarespace & google workspace. URLs include brenvalecoaching.example and brenvale4kids.example. I have an idea of what I am looking for in a website and I have some examples of website designs I like, but I am 100% open to your design concepts and artistic flair. email is torin@brenvalecoaching.example
I am looking for someone to design the site, help me understand how to make "minor" changes and hopefully have a long term relationship on the tech side of the business. I need an Idea of pricing for future changes (Rate T&M).
There are 2 businesses so I need a way to incorporate both the main company and a subsidiary into 1 website or link it somehow. I am open to your suggestions how to accomplish that. Do I need 2 completely separate websites or can it be done on 1 site directing you to different pages. I read conflicting info if it is a BAD idea to link 2 different websites so I will defer to your advice.
Below are the pages I need designed:
- Home Page- BrenVale Coaching
- Home Page- BrenVale 4 Kids (Homeschool market)
- Member Page (subscription service?)
- Workouts- with video clips 1-6 min each
- About
- Contact
- FAQ's
Future work & page designs:
- Store with training subscriptions & a few merch items
- Booking Appointments
- Bookshelf
- email campaign
-Blog
I like the feel of this website:
https://zestlope.example/

```html
<!DOCTYPE html>
<html lang="en">
<head>
<meta charset="utf-8">
<title>BrenVale Coaching</title>
<link href="https://fonts.googleapis.com/css2?family=Rubik:wght@400;700&family=Roboto:wght@400;500;700&display=swap" rel="stylesheet">
<style>
:root{
  --ink:#111111;
  --text:#333333;
  --muted:#777777;
  --paper:#ffffff;
  --band:#f4f4f4;
  --dark:#1c1c1c;
}
*{box-sizing:border-box;margin:0;padding:0}
html,body{width:1200px;height:3595px;overflow:hidden;background:var(--paper)}
body{position:relative;font-family:'Roboto',sans-serif;color:var(--text)}
.abs{position:absolute}
.photo{position:absolute}
.btn{position:absolute;display:flex;align-items:center;justify-content:center;background:var(--ink);color:#fff;font:700 14px 'Roboto',sans-serif;text-decoration:none}
.heading{font-family:'Rubik',sans-serif;font-weight:400;color:var(--ink);letter-spacing:.5px}
.heading b{font-weight:700}

/* header */
.brand{left:112px;top:7px;width:136px;height:93px;display:flex;flex-direction:column;align-items:center;justify-content:flex-end}
.brand-mark{width:34px;height:34px;border-radius:50%;background:var(--ink);margin-bottom:12px}
.brand-name{font:400 19px 'Roboto',sans-serif;letter-spacing:5px;color:var(--ink)}
.nav{left:487px;top:44px;display:flex;gap:22px;font:500 14px 'Roboto',sans-serif;color:var(--ink)}
.nav a{color:inherit;text-decoration:none;padding-bottom:6px}
.nav a.active{border-bottom:2px solid var(--ink)}
.signup{left:985px;top:29px;width:103px;height:48px}

/* welcome */
.welcome-title{left:0;width:1200px;top:143px;text-align:center;font-size:28px}
.welcome-text{left:140px;width:920px;top:193px;text-align:center;font-size:15px;line-height:26px;color:#444}
.caption{font:500 18px 'Roboto',sans-serif;color:var(--ink);text-decoration:underline;text-underline-offset:3px;text-align:center}

/* about */
.about-title{left:112px;top:1040px;font-size:27px}
.about-text{left:112px;width:441px;font-size:14px;line-height:26px;color:var(--muted);text-align:justify}

/* services */
.services{left:0;top:1592px;width:1200px;height:749px;background:var(--band)}
.services-title{left:0;width:1200px;top:1653px;text-align:center;font-size:32px}
.service-name{width:308px;text-align:center;font:500 18px 'Roboto',sans-serif;color:var(--ink);top:2120px}
.service-text{width:308px;text-align:center;font-size:14px;line-height:26px;color:var(--muted);top:2152px;padding:0 20px}

/* blog */
.blog-title{left:110px;top:2420px;font-size:32px}
.post-title{width:231px;font:500 15px 'Roboto',sans-serif;line-height:22px;color:var(--ink)}
.post-date{width:231px;font-size:13px;color:var(--muted);display:flex;align-items:center;gap:8px}

/* cta */
.cta{left:0;top:3031px;width:1200px;height:370px;background:linear-gradient(100deg,#2a2622,#3b332c 45%,#24201d)}
.cta-title{left:0;width:1200px;top:3097px;text-align:center;font-size:32px;color:#fff}
.cta-text{left:130px;width:940px;top:3161px;text-align:center;font-size:14.5px;line-height:26px;color:#eee}
.cta-btn{left:492px;top:3278px;width:215px;height:49px;background:#fff;color:var(--ink)}

/* footer */
.footer{left:0;top:3401px;width:1200px;height:194px;background:var(--band)}
.foot-brand{left:112px;top:3432px;width:136px;height:100px}
.copyright{left:112px;top:3552px;font-size:13px;color:var(--muted)}
.news-title{left:558px;top:3472px;font:500 17px 'Roboto',sans-serif;color:var(--ink)}
.news-form{left:558px;top:3520px;width:527px;height:49px;background:#fff;display:flex;align-items:center;justify-content:space-between;padding:4px 4px 4px 17px}
.news-form span{font-size:13px;color:var(--muted)}
.news-form .btn{position:static;width:104px;height:100%}
</style>
</head>
<body>

<header>
  <div class="abs brand">
    <div class="brand-mark"></div>
    <div class="brand-name">BRENVALE</div>
  </div>
  <nav class="abs nav">
    <a class="active">HOME</a><a>ABOUT</a><a>WORKOUTS</a><a>MEMBER</a><a>FAQ'S</a><a>CONTACT</a>
  </nav>
  <a class="btn signup">SIGN UP</a>
</header>

<section>
  <h1 class="abs heading welcome-title">WELCOME TO <b>BRENVALE COACHING</b></h1>
  <p class="abs welcome-text">Lorem ipsum dolor sit amet, consectetur adipiscing elit, sed do eiusmod tempor incididunt ut labore et dolore magna aliqua. Ut enim ad minim veniam, quis nostrud exercitation ullamco laboris nisi ut aliquipea.</p>
  <div class="photo" role="img" aria-label="Group gym workout with dumbbells" style="left:112px;top:289px;width:471px;height:556px;background:linear-gradient(160deg,#8f8a82,#4a4a4a 55%,#2b2c2e)"></div>
  <div class="abs caption" style="left:112px;width:471px;top:866px">BRENVALE COACHING</div>
  <div class="photo" role="img" aria-label="Parent and child stretching on yoga mats at home" style="left:730px;top:335px;width:358px;height:464px;background:linear-gradient(170deg,#e4e2df,#c9c4bf 60%,#8d8c8b)"></div>
  <div class="abs caption" style="left:730px;width:358px;top:820px">BRENVALE 4 KIDS</div>
</section>

<section>
  <h2 class="abs heading about-title">ABOUT <b>BRENVALE</b></h2>
  <p class="abs about-text" style="top:1110px">Sed ut perspiciatis unde omnis iste natus error sit voluptatem accus antium doloremque laudantium, totam rem aperiam, eaque ipsa quae ab illo inventore veritatis et quasi architecto beatae vitae dicta sunt explicabmo enim ipsam voluptatem.</p>
  <p class="abs about-text" style="top:1229px">Perspiciatis unde omnis iste natus error sit voluptatem accus antium doloremque laudantium, totam rem aperiam, eaque ipsa quae ab illo inventore veritatis et quasi architecto beatae vitae dicta sunt explicabmo enim ipsam voluptatem.</p>
  <a class="btn" style="left:112px;top:1373px;width:129px;height:50px">LEARN MORE</a>
  <div class="photo" role="img" aria-label="Trainer coaching a client through a dumbbell exercise" style="left:617px;top:979px;width:471px;height:514px;background:linear-gradient(165deg,#c9ced2,#6f7478 50%,#34373b)"></div>
</section>

<section>
  <div class="abs services"></div>
  <h2 class="abs heading services-title">OUR <b>SERVICES</b></h2>

  <div class="photo" role="img" aria-label="Personal trainer reviewing a plan with a client" style="left:112px;top:1754px;width:308px;height:341px;background:linear-gradient(170deg,#d7d8d8,#9a9a99 60%,#4c4c4c)"></div>
  <h3 class="abs service-name" style="left:112px">PERSONAL TRAINING</h3>
  <p class="abs service-text" style="left:112px">Sed ut perspiciatis unde omnis iste natus err or sit voluptatem accus antium.</p>
  <a class="btn" style="left:189px;top:2225px;width:154px;height:49px">SUBSCRIBE NOW</a>

  <div class="photo" role="img" aria-label="Woman doing a plank workout in front of a laptop" style="left:445px;top:1754px;width:308px;height:341px;background:linear-gradient(170deg,#8c8c7c,#6b6c63 50%,#3e8e86 80%,#b48b5e)"></div>
  <h3 class="abs service-name" style="left:445px">ONLINE TRAINING</h3>
  <p class="abs service-text" style="left:445px">Sed ut perspiciatis unde omnis iste natus err or sit voluptatem accus antium.</p>
  <a class="btn" style="left:522px;top:2225px;width:154px;height:49px">SUBSCRIBE NOW</a>

  <div class="photo" role="img" aria-label="Woman drinking water beside fresh fruit" style="left:780px;top:1754px;width:308px;height:341px;background:linear-gradient(170deg,#ece7e1,#c2a58e 55%,#c9a24a 85%)"></div>
  <h3 class="abs service-name" style="left:780px">NUTRITIONAL GUIDANCE</h3>
  <p class="abs service-text" style="left:780px">Sed ut perspiciatis unde omnis iste natus err or sit voluptatem accus antium.</p>
  <a class="btn" style="left:857px;top:2225px;width:154px;height:49px">SUBSCRIBE NOW</a>
</section>

<section>
  <h2 class="abs heading blog-title">LATEST <b>BLOG</b></h2>

  <div class="photo" role="img" aria-label="Two women stretching on yoga mats" style="left:112px;top:2497px;width:231px;height:214px;background:linear-gradient(170deg,#d8d2cc,#b9a9b8 70%,#c79bc8)"></div>
  <p class="abs post-title" style="left:112px;top:2724px">Sed ut perspiciatis unde omnis iste naiciatis undtus</p>
  <p class="abs post-date" style="left:112px;top:2779px"><svg width="12" height="12" viewBox="0 0 12 12"><rect x="1" y="2" width="10" height="9" fill="none" stroke="#555" stroke-width="1.4"/><line x1="1" y1="5" x2="11" y2="5" stroke="#555" stroke-width="1.4"/></svg>31 Jan 2022</p>

  <div class="photo" role="img" aria-label="Group class doing push-ups" style="left:360px;top:2497px;width:231px;height:285px;background:linear-gradient(170deg,#6c6862,#4d4c4b 60%,#2f3033)"></div>
  <p class="abs post-title" style="left:360px;top:2795px">Sed ut perspiciatis unde omnis iste naiciatis undtus</p>
  <p class="abs post-date" style="left:360px;top:2850px"><svg width="12" height="12" viewBox="0 0 12 12"><rect x="1" y="2" width="10" height="9" fill="none" stroke="#555" stroke-width="1.4"/><line x1="1" y1="5" x2="11" y2="5" stroke="#555" stroke-width="1.4"/></svg>31 Jan 2022</p>

  <div class="photo" role="img" aria-label="Parent and child exercising at home" style="left:608px;top:2497px;width:232px;height:214px;background:linear-gradient(170deg,#ddd9d4,#a49a92 60%,#d9a43a 85%)"></div>
  <p class="abs post-title" style="left:608px;top:2724px">Sed ut perspiciatis unde omnis iste naiciatis undtus</p>
  <p class="abs post-date" style="left:608px;top:2779px"><svg width="12" height="12" viewBox="0 0 12 12"><rect x="1" y="2" width="10" height="9" fill="none" stroke="#555" stroke-width="1.4"/><line x1="1" y1="5" x2="11" y2="5" stroke="#555" stroke-width="1.4"/></svg>31 Jan 2022</p>

  <div class="photo" role="img" aria-label="Pair training with kettlebells in a dark gym" style="left:857px;top:2497px;width:231px;height:285px;background:linear-gradient(170deg,#3a3b3d,#5a4a40 50%,#22232a)"></div>
  <p class="abs post-title" style="left:857px;top:2795px">Sed ut perspiciatis unde omnis iste naiciatis undtus</p>
  <p class="abs post-date" style="left:857px;top:2850px"><svg width="12" height="12" viewBox="0 0 12 12"><rect x="1" y="2" width="10" height="9" fill="none" stroke="#555" stroke-width="1.4"/><line x1="1" y1="5" x2="11" y2="5" stroke="#555" stroke-width="1.4"/></svg>31 Jan 2022</p>

  <a class="btn" style="left:518px;top:2903px;width:163px;height:49px">MORE BLOG POSTS</a>
</section>

<section>
  <div class="abs cta" role="img" aria-label="Dimmed photo of people stretching outdoors"></div>
  <h2 class="abs heading cta-title" style="color:#fff">GET READY <b>TO START?</b></h2>
  <p class="abs cta-text">Sed ut perspiciatis unde omnis iste natus error sit voluptatem accus antium doloremque laudantium, totam rem aperiam, eaque ipsa quae ab illo inventore veritatis et quasi architecto beatae vitae dicta sunt explte natus error sit voluptatem accus antium doloremque laudantium, totam rem aperiam, eaque ipsa quae ab illo dicta sunt explicabmo icabmo enim ipsam voluptatem.</p>
  <a class="btn cta-btn">BOOKING APPOINTMENTS</a>
</section>

<footer>
  <div class="abs footer"></div>
  <div class="abs brand foot-brand">
    <div class="brand-mark"></div>
    <div class="brand-name">BRENVALE</div>
  </div>
  <p class="abs copyright">© 2022 All Rights Reserved</p>
  <h3 class="abs news-title">SUBSCRIBE TO OUR NEWSLETTER</h3>
  <div class="abs news-form"><span>Email Address</span><a class="btn">SIGN UP</a></div>
</footer>

</body>
</html>
```